Business Cards for a law firm

Business cards for our law firm. Use our silhoette logo and OAK PARTNERS - check our website (www.oakpartners.example)

Contact Information for Business Card

our silhouette logo, OAK PARTNERS, 800-555-0147, Dorian Pemberton, dorian@oakpartners.example

Requirements
Must have
• our silhouette logo, OAK PARTNERS, 800-555-0147, Dorian Pemberton, dorian@oakpartners.example

```html
<!DOCTYPE html>
<html lang="en">
<head>
<meta charset="utf-8">
<title>Oak Partners – Business Cards</title>
<link href="https://fonts.googleapis.com/css2?family=Cinzel:wght@600;700&family=Arimo:wght@400&display=swap" rel="stylesheet">
<style>
  :root {
    --navy: #1a2f6b;
    --navy-back: #182f69;
    --navy-light: #4f86d6;
    --slate: #555555;
    --paper: #f4f4f5;
    --ink: #222630;
    --rule: #9a9ca3;
    --backdrop: #e3e3e3;
  }
  * { margin: 0; padding: 0; box-sizing: border-box; }
  html, body { width: 1200px; height: 1040px; overflow: hidden; }
  body { background: var(--backdrop); position: relative; font-family: "Arimo", Arial, sans-serif; }

  .card {
    position: absolute;
    left: 282px;
    width: 642px;
    height: 366px;
    border-radius: 18px;
    overflow: hidden;
  }
  .card--front { top: 130px; background: var(--paper); }
  .card--back { top: 568px; background: var(--navy-back); }

  .wordmark {
    position: absolute;
    font-family: "Cinzel", serif;
    font-weight: 700;
    white-space: nowrap;
    letter-spacing: 0.12em;
  }
  .card--front .wordmark {
    left: 62px; top: 164px;
    font-size: 19px;
    color: var(--navy);
  }
  .card--back .wordmark {
    left: 0; right: 0; top: 154px;
    text-align: center;
    font-size: 36px;
    color: var(--navy-light);
  }

  .divider {
    position: absolute;
    left: 326px; top: 125px;
    width: 1px; height: 118px;
    background: var(--rule);
  }

  .holder-name {
    position: absolute;
    left: 345px; top: 124px;
    font-family: "Cinzel", serif;
    font-weight: 700;
    font-size: 21px;
    letter-spacing: 0.03em;
    color: var(--navy);
    white-space: nowrap;
  }

  .contact-list {
    position: absolute;
    left: 345px; top: 175px;
    list-style: none;
  }
  .contact-list li {
    display: flex;
    align-items: center;
    height: 20px;
    font-size: 16px;
    color: var(--ink);
    white-space: nowrap;
  }
  .contact-list svg { width: 13px; height: 13px; margin-right: 9px; flex: none; fill: var(--navy); }

  .footer-band { position: absolute; left: 0; bottom: 0; width: 100%; height: 18px; }
</style>
</head>
<body>

<section class="card card--front" aria-label="Business card front">
  <div class="wordmark">OAK PARTNERS</div>
  <div class="divider"></div>
  <h1 class="holder-name">Dorian Pemberton</h1>
  <ul class="contact-list">
    <li>
      <svg viewBox="0 0 16 16" aria-hidden="true"><path d="M3.6 1.2l2.3 2.6c.4.4.4 1 0 1.4L4.8 6.4c.9 2 2.5 3.7 4.6 4.7l1.2-1.2c.4-.4 1-.4 1.4 0l2.6 2.3c.4.4.4 1 0 1.4l-1.3 1.3C12 15.9 10 15.6 7.6 14 5 12.3 3 10 1.7 7.4.6 5.2.3 3.6 1 2.6L2.2 1.2c.4-.4 1-.4 1.4 0z"/></svg>
      800-555-0147
    </li>
    <li>
      <svg viewBox="0 0 16 16" aria-hidden="true"><path d="M1 3h14v10H1z M2 4.2v.3l6 4.2 6-4.2v-.3z" fill-rule="evenodd"/></svg>
      dorian@oakpartners.example
    </li>
    <li>
      <svg viewBox="0 0 16 16" aria-hidden="true"><circle cx="8" cy="8" r="7"/><path d="M5 4c1 0 2 1 1.6 2S4.5 7 5 8.5 7 9 7 11s-1 2.5-1.5 2.5C3.5 12.5 2.5 10 2.7 8 3 6 4 4.2 5 4zM10 3.5c1.5.5 2.5 2 2 3-.6 1-1.8.5-2.2-.5-.3-1 .2-2.5.2-2.5z" fill="var(--paper)"/></svg>
      www.oakpartners.example
    </li>
  </ul>
  <svg class="footer-band" viewBox="0 0 642 18" preserveAspectRatio="none" aria-hidden="true">
    <polygon points="0,0 421,0 416,18 0,18" fill="var(--navy)"/>
    <polygon points="426,0 642,0 642,18 421,18" fill="var(--slate)"/>
  </svg>
</section>

<section class="card card--back" aria-label="Business card back">
  <div class="wordmark">OAK PARTNERS</div>
</section>

</body>
</html>
```